Brindle Children's Center - Child Care brochure

I just bought a new child care and completely renovated the space. We are also designing a new website, so I need the brochure to match that with updated info. www.brindlechildrenscenter.com - Information on there is current. We expect to have the new one up and running in the next few days. We have new photo's that I'd like to be added to the flyer too. ps. the boys in the pictures are mine, so i would appreciate one of them being added :). support@netcrafterhub.com has details on the website (dev.brindlechildrenscenter.com). The child care program is only open during the ski season - i.e. a resort facility catering to high end clients.
I'm attaching the the website information, the flyer I created, logo files and pictures.

Target Market(s)

Parents of young children

Font styles to use
Other font styles liked:
• "Things we said" & "Calibri Light"

Colors
cfeae6
fef1ee

Requirements
Must have
• Pictures of children. sleek design - winter, mountain theme. Check with website designer on new website.
Nice to have
• prices included
Should not have
• Kid like artwork

```html
<!DOCTYPE html>
<html lang="en">
<head>
<meta charset="utf-8">
<title>Brindle Children's Center – Brochure Inside</title>
<link rel="stylesheet" href="https://fonts.googleapis.com/css2?family=Lato:wght@300;400&family=Caveat:wght@500&display=swap">
<style>
  :root {
    --paper: #fef1ee;
    --mint: #6cc6a0;
    --mint-soft: #cfeae6;
    --ink: #3f3f3f;
    --ink-soft: #555;
    --script: #4a5560;
    --white: #ffffff;
  }
  * { box-sizing: border-box; margin: 0; padding: 0; }
  html, body { width: 1200px; height: 923px; overflow: hidden; background: var(--paper); }
  body { font-family: "Lato", sans-serif; font-weight: 300; color: var(--ink); position: relative; }

  .panel { position: absolute; top: 36px; width: 327px; font-size: 12.4px; line-height: 1.52; }
  .panel--services { left: 33px; }
  .panel--program { left: 436px; }
  .panel--staff { left: 830px; }

  .section-title {
    background: var(--mint); color: var(--ink); font-weight: 400;
    font-size: 18px; line-height: 22px; padding: 0 8px; margin-bottom: 10px;
  }
  .panel p { text-align: justify; margin-bottom: 16px; }
  .panel p.lead-in { text-align: left; margin-bottom: 8px; }
  .activity-list, .bring-list { list-style: none; margin-bottom: 16px; }
  .activity-list li, .bring-list li { padding-left: 10px; position: relative; }
  .activity-list li::before, .bring-list li::before {
    content: ""; position: absolute; left: 0; top: 8px; width: 4px; height: 4px;
    border-radius: 50%; background: var(--mint);
  }
  .bring-list li { text-align: justify; margin-bottom: 2px; }
  .section-title--spaced { margin-top: 22px; }

  .rate-label { margin: 6px 0 6px; }
  .rate-table { border-collapse: collapse; width: 250px; margin: 0 0 18px 6px; font-size: 12.4px; }
  .rate-table td { border: 1.5px solid var(--mint); height: 29px; padding: 0 18px; }
  .rate-table td.price { width: 70px; padding: 0 12px; }

  .quote {
    position: absolute; left: 290px; top: 558px; width: 560px;
    font-family: "Caveat", cursive; font-weight: 500; color: var(--script);
    font-size: 50px; line-height: 54px; text-align: center;
  }
  .quote-ornament { position: absolute; left: 755px; top: 585px; width: 70px; height: 36px; }

  .photo-band { position: absolute; left: 0; top: 718px; width: 1200px; height: 8px; background: var(--mint); }
  .photo-strip { position: absolute; left: 0; top: 726px; width: 1200px; height: 197px; background: var(--white); }
  .photo { position: absolute; }
  .photo--boy { left: 0; top: 548px; width: 233px; height: 375px; background: linear-gradient(180deg, #d9cfc6, #2c3550 70%, #26304a); }
  .photo--reading { left: 254px; top: 737px; width: 200px; height: 170px; background: linear-gradient(135deg, #d8c2a8, #8f7f78); }
  .photo--dress { left: 462px; top: 737px; width: 170px; height: 170px; background: linear-gradient(135deg, #e6c86a, #c9a48c); }
  .photo--crafts { left: 638px; top: 737px; width: 197px; height: 170px; background: linear-gradient(135deg, #b7a7a2, #6d5f7a); }
  .photo--table { left: 842px; top: 737px; width: 144px; height: 170px; background: linear-gradient(135deg, #c7b9a4, #5f6a7d); }
  .photo--puzzle { left: 993px; top: 737px; width: 207px; height: 170px; background: linear-gradient(135deg, #b9c2c6, #b08f9c); }
</style>
</head>
<body>

<section class="panel panel--services">
  <h2 class="section-title">Our Services</h2>
  <p>The Brindle Children's Center is a full service childcare facility that caters to children from six weeks to nine years old. Infants, toddlers, and young children can explore the activities and toys available in the Center. Children ages four and older have the option to join Brindle's legendary Ridgeline Ski School and spend part or all of the day learning from one of Brindle's friendly instructors.</p>
  <p class="lead-in">Children visiting the center can look forward to the following activities:</p>
  <ul class="activity-list">
    <li>Dramatic play</li>
    <li>Arts and Crafts</li>
    <li>Discovery Science</li>
    <li>Snow Play</li>
    <li>Games</li>
    <li>Music</li>
    <li>Nutritious lunch and snacks</li>
  </ul>
</section>

<section class="panel panel--program">
  <h2 class="section-title">Our Program</h2>
  <p>The Brindle Children's Center is fully accredited by the State of Utah and offers a program that caters to your child's needs:</p>
  <p>Infant Care – Our infant care program is open to children over six weeks. We will tailor a program to meet your child's daily schedule. Pagers are available for nursing mothers and concerned parents.</p>
  <p>Toddlers – Children ages 18-months to three years want to explore just about everything! Creative art projects, musical games, and large muscle activities will keep your little one active and happy all day.</p>
  <p>Ages Three and Up – With their teacher and new friends, your child will explore the wonder of Brindle snow, enjoy art projects, and choose from a variety of activities that challenge the imagination.</p>
  <p>Ski School – The Brindle Children's Center works closely with the famous Ridgeline Ski School. If you wish to have your child (ages 4 and up) participate in a group ski lesson, we will take your child to meet their ski class and pick them up after. Private lessons are also available for any age.</p>
</section>

<section class="panel panel--staff">
  <h2 class="section-title">Our Staff</h2>
  <p>At the Brindle Children's Center our staff takes pride in creating a nurturing and creative atmosphere where your child can learn and grow. Each member of our staff is continuously trained in Early Childhood Education, CPR and first aid. We work together as a team to provide the best care possible for your child.</p>

  <h2 class="section-title section-title--spaced">Things to bring with you:</h2>
  <ul class="bring-list">
    <li>For Infants, parents should supply diapers, wipes, a change of clothes, strained food (yum), and formula.</li>
    <li>For Toddlers, parents should supply diapers, wipes, and a change of clothes.</li>
    <li>For Ages 3 and Up, parents should supply a change of clothes, snow gear including: coat, hat, gloves, and snow pants, boots, and eye protection (sun glasses or goggles).</li>
  </ul>

  <h2 class="section-title section-title--spaced">Rates</h2>
  <p class="rate-label">Infant/Toddler:</p>
  <table class="rate-table">
    <tr><td>Full Day</td><td class="price">$105</td></tr>
    <tr><td>Half Day</td><td class="price">$90</td></tr>
    <tr><td>Five Day Package</td><td class="price">$475</td></tr>
  </table>
  <p class="rate-label">3 Years and Up:</p>
  <table class="rate-table">
    <tr><td>Full Day</td><td class="price">$99</td></tr>
    <tr><td>Half Day</td><td class="price">$85</td></tr>
    <tr><td>Five Day Package</td><td class="price">$450</td></tr>
  </table>
</section>

<p class="quote">Blessed are the curious,<br>for they shall have adventures.</p>
<svg class="quote-ornament" role="img" aria-label="Small bird on a leafy branch ornament" viewBox="0 0 70 36">
  <rect width="70" height="36" rx="4" fill="#9aa3ab" opacity="0.35"/>
</svg>

<div class="photo-band"></div>
<div class="photo-strip"></div>
<div class="photo photo--boy" role="img" aria-label="Photo of a smiling young boy in a navy sweater holding a toy plane"></div>
<div class="photo photo--reading" role="img" aria-label="Photo of a toddler reading a picture book beside a teddy bear"></div>
<div class="photo photo--dress" role="img" aria-label="Photo of a young girl in a yellow dress-up gown"></div>
<div class="photo photo--crafts" role="img" aria-label="Photo of two girls doing crafts at a table"></div>
<div class="photo photo--table" role="img" aria-label="Photo of two children playing together at an activity table"></div>
<div class="photo photo--puzzle" role="img" aria-label="Photo of two girls working on a puzzle"></div>

</body>
</html>
```